Luxury Wine Label for New Startup Winery

We need a wine label for our new winery startup. We have worked with a local designer but do not feel the resulting label / logo have the elevation required to present our brand as a luxury wine. Our winery is called "Quailbrook Vineyards" and we are focused on extremely high quality hand crafted artisan and estate wines from the Pacific Northwest.
We would like to see designs that utilize a tree line, or other imagery that represents the "Quailbrook" part of our company name. Another interesting feature could be wood grain.
A logo will be required based on your design so please design with this in mind:
This logo should be consistent with the wine bottle label design, and should be representative of our high end exclusive wine while giving a sense of place (Oregon/ Pacific Northwest.)
I will supply an image of the design we received from our local designer, PLEASE NOTE: in general we do like wood grain and tree line concepts but feel the execution was poorly done.
ATTN: Logo design should be suitable for use on: Bottles (Red wine/rose/white wine), Bussiness cards, vehicle signage, business signage, etc
P.S.:
If you have a design that is not outside the box we are still interested in seeing it.
Label is for a burgundy style bottle with a label height of 3.5 - 4" and a width of 3.5-4"
any label <= 4"x4" and >=3.5"x3.5" will be acceptable:
HOWEVER Width should be greater than or equal to height due to the bottle format
Target Market(s)
Wine enthusiasts with adequate discretionary budgets to afford $100 bottles of wine.
Industry/Entity Type
Wine / Winery
Requirements
Must have
- A sense of luxury, a feel of exclusivity, and a theme consistent with our product and brand name
Nice to have
- Tree line, wood grain or other wood themes. Serif fonts
Should not have
- anything cheesy, off topic, hard to read script fonts or anything that makes the label hard to read from a few feet away or too busy

```html
<!DOCTYPE html>
<html lang="en">
<head>
<meta charset="utf-8">
<title>Quailbrook Vineyards — 2024 Syrah</title>
<link rel="stylesheet" href="https://fonts.googleapis.com/css2?family=Cinzel:wght@400&family=Cormorant+Garamond:wght@300&family=Josefin+Sans:wght@400&display=swap">
<style>
  :root {
    --copper: #b57a5e;
    --night: #000000;
    --mist: #48474d;
    --forest: #1a191d;
    --glass: #141316;
    --glass-edge: #2c2b30;
    --label-light: #9a999c;
    --label-dark: #1d1a1c;
  }
  * { margin: 0; padding: 0; box-sizing: border-box; }
  html, body {
    width: 912px;
    height: 1200px;
    overflow: hidden;
    background: var(--night);
  }
  .poster {
    position: relative;
    width: 912px;
    height: 1200px;
    background: var(--night);
    overflow: hidden;
  }
  .forest-backdrop {
    position: absolute;
    left: 0;
    top: 0;
    width: 912px;
    height: 640px;
    background:
      radial-gradient(ellipse 210px 300px at 357px 330px, rgba(120,118,126,0.5), rgba(0,0,0,0) 75%),
      radial-gradient(ellipse 200px 320px at 700px 220px, rgba(90,92,88,0.35), rgba(0,0,0,0) 75%),
      linear-gradient(180deg, var(--forest) 0%, #2a292e 40%, #1a191c 75%, var(--night) 100%);
  }
  .artwork {
    position: absolute;
    left: 0;
    top: 0;
    width: 912px;
    height: 1200px;
  }
  .mark-circle { fill: none; stroke: var(--copper); stroke-width: 1.5; }
  .rule { stroke: var(--copper); stroke-width: 1.2; }
  .brand-name {
    font-family: "Cinzel", serif;
    font-size: 43px;
    fill: var(--copper);
  }
  .brand-sub {
    font-family: "Cinzel", serif;
    font-size: 20px;
    fill: var(--copper);
  }
  .seal-arc {
    font-family: "Josefin Sans", sans-serif;
    font-size: 15px;
    letter-spacing: 4px;
    fill: var(--copper);
  }
  .seal-year {
    font-family: "Josefin Sans", sans-serif;
    font-size: 17px;
    letter-spacing: 3px;
    fill: var(--copper);
  }
  .seal-varietal {
    font-family: "Cormorant Garamond", serif;
    font-weight: 300;
    font-size: 84px;
    fill: var(--copper);
  }
  .bottle-text-name { font-family: "Cinzel", serif; font-size: 15px; fill: var(--copper); }
  .bottle-text-sub { font-family: "Cinzel", serif; font-size: 7px; fill: var(--copper); }
  .bottle-text-year { font-family: "Josefin Sans", sans-serif; font-size: 7px; fill: var(--copper); }
  .bottle-text-varietal { font-family: "Cormorant Garamond", serif; font-weight: 300; font-size: 22px; fill: var(--copper); }
</style>
</head>
<body>
  <main class="poster">
    <div class="forest-backdrop" role="img" aria-label="Misty dark conifer forest at dusk"></div>

    <svg class="artwork" viewBox="0 0 912 1200" width="912" height="1200">
      <defs>
        <linearGradient id="glass-shade" x1="0" y1="0" x2="1" y2="0">
          <stop offset="0" stop-color="var(--glass-edge)"/>
          <stop offset="0.35" stop-color="var(--glass)"/>
          <stop offset="1" stop-color="#0b0a0c"/>
        </linearGradient>
        <linearGradient id="label-shade" x1="0" y1="0" x2="1" y2="1">
          <stop offset="0" stop-color="var(--label-light)"/>
          <stop offset="0.6" stop-color="#3a393d"/>
          <stop offset="1" stop-color="var(--label-dark)"/>
        </linearGradient>
        <path id="seal-top" d="M 264 590 A 93 93 0 0 1 450 590"/>
        <path id="seal-bottom" d="M 245 590 A 112 112 0 0 0 469 590"/>
      </defs>

      <!-- Brand lockup -->
      <g class="brand-lockup">
        <circle class="mark-circle" cx="357" cy="240" r="62"/>
        <line class="rule" x1="153" y1="312" x2="561" y2="312"/>
        <text class="brand-name" x="160" y="364" textLength="397" lengthAdjust="spacing">QUAILBROOK</text>
        <line class="rule" x1="153" y1="394" x2="244" y2="394"/>
        <text class="brand-sub" x="250" y="401" textLength="214" lengthAdjust="spacing">VINEYARDS</text>
        <line class="rule" x1="470" y1="394" x2="561" y2="394"/>
      </g>

      <!-- Vintage seal -->
      <g class="seal" aria-label="Willamette Valley 2024 Syrah">
        <text class="seal-arc"><textPath href="#seal-top" startOffset="50%" text-anchor="middle">WILLAMETTE VALLEY</textPath></text>
        <text class="seal-year" x="357" y="558" text-anchor="middle">2024</text>
        <text class="seal-varietal" x="290" y="622" textLength="134" lengthAdjust="spacingAndGlyphs">SYRAH</text>
        <text class="seal-arc"><textPath href="#seal-bottom" startOffset="50%" text-anchor="middle">45.2841° N, 123.0417° W</textPath></text>
      </g>

      <!-- Bottle -->
      <g class="bottle" role="img" aria-label="Burgundy-style wine bottle wearing the Quailbrook Syrah label">
        <path fill="url(#glass-shade)" d="M 692 30 L 802 30 L 802 80 L 798 92 L 800 220 C 806 290 830 330 858 400 C 880 460 888 520 888 600 L 890 1168 Q 890 1178 878 1178 L 620 1178 Q 608 1178 608 1168 L 608 600 C 608 520 616 460 636 400 C 662 330 688 290 694 220 L 696 92 L 692 80 Z"/>
        <rect x="721" y="95" width="49" height="118" fill="#8a5e4a"/>
        <rect x="615" y="755" width="262" height="301" fill="url(#label-shade)"/>
        <text class="bottle-text-name" x="667" y="882" textLength="158" lengthAdjust="spacing">QUAILBROOK</text>
        <text class="bottle-text-sub" x="746" y="897" text-anchor="middle" letter-spacing="2">VINEYARDS</text>
        <text class="bottle-text-year" x="746" y="961" text-anchor="middle" letter-spacing="1">2024</text>
        <text class="bottle-text-varietal" x="720" y="989" textLength="52" lengthAdjust="spacingAndGlyphs">SYRAH</text>
      </g>
    </svg>
  </main>
</body>
</html>
```